Northvale Strategy Partners Website Design

I need a website design for my new business consulting and executive coaching firm, Northvale Strategy Partners. We provide consultative services to business C-suites as well as personal coaching to executives. I have attached the logo with color scheme I have chosen. I would like the website to reflect professionalism and continue the color scheme in the logo.

Target Market(s)

Small to medium business and their executives; middle to upper income men and women in mid- to late career looking for significance

Industry/Entity Type

Business Consultant

Number of Pages Required

4 page

Requirements
Must have
• A homepage with prominent logo and way to contact for more information; an area on the homepage with easy to read, clear text to describe what the company does; a prominent area on the homepage for a tagline; a blog page that can be updated regularly, an "about us" page with biographical information; an "about us" page; a page detailing services offered
• The web design must match the logo colors and font that I have uploaded.
Nice to have
• A lighthouse picture in the background or header
Should not have
• A lot of text area on the homepage

```html
<!DOCTYPE html>
<html lang="en">
<head>
<meta charset="utf-8">
<title>Northvale Strategy Partners</title>
<link href="https://fonts.googleapis.com/css2?family=Raleway:wght@500;600;700&family=Open+Sans:ital,wght@0,400;0,600;0,700;1,400&display=swap" rel="stylesheet">
<style>
:root{
  --navy:#1d2b5c;
  --navy-deep:#14204a;
  --maroon:#7b1419;
  --text:#6b6b6b;
  --text-dark:#333;
  --line:#e4e4e4;
  --footer:#2f2f2f;
  --footer-bottom:#252525;
  --footer-text:#8a8a8a;
  --white:#fff;
}
*{box-sizing:border-box;margin:0;padding:0}
html,body{width:1200px;height:2956px;overflow:hidden}
body{font-family:"Open Sans",Arial,sans-serif;color:var(--text);background:var(--white);position:relative}
section,header,footer{position:absolute;left:0;width:1200px}
.abs{position:absolute}

/* header */
.site-header{top:0;height:105px;background:var(--white)}
.brand{left:100px;top:30px;display:flex;align-items:center;gap:12px}
.brand-mark{width:34px;height:34px;background:var(--navy)}
.brand-name{font-family:"Raleway",sans-serif;font-weight:700;font-size:19px;color:var(--navy);line-height:1.15;width:190px}
.contact-bar{right:100px;top:22px;display:flex;gap:34px;font-size:12.5px;color:var(--text)}
.contact-bar span{display:flex;align-items:center;gap:8px}
.contact-bar b{color:var(--maroon);font-weight:600}
.main-nav{right:100px;top:68px;display:flex;gap:60px;font-size:12px;color:#555;letter-spacing:.3px}

/* hero */
.hero{top:105px;height:503px}
.hero-photo{position:absolute;inset:0;background:linear-gradient(180deg,#6f95c6 0%,#a9c3df 35%,#8a8f7a 55%,#6e6558 75%,#54606a 100%)}
.hero-title{right:514px;top:80px;text-align:right;font-family:"Raleway",sans-serif;font-weight:700;font-size:21px;line-height:32px;color:var(--white);letter-spacing:.6px}
.hero-dots{left:560px;top:482px;display:flex;gap:7px}
.hero-dots i{width:8px;height:8px;border-radius:50%;background:rgba(255,255,255,.6)}
.hero-dots i:first-child{background:var(--white)}

/* welcome */
.welcome{top:608px;height:600px}
.welcome-kicker{left:124px;top:100px;font-family:"Raleway",sans-serif;font-weight:500;font-size:23px;color:var(--navy);letter-spacing:.5px}
.welcome-title{left:124px;top:134px;font-family:"Raleway",sans-serif;font-weight:700;font-size:24px;color:var(--navy);letter-spacing:.5px}
.welcome-copy{left:124px;top:190px;width:460px;font-size:12.5px;line-height:25px}
.welcome-copy p+p{margin-top:20px}
.btn{display:inline-flex;align-items:center;justify-content:center;background:var(--maroon);color:var(--white);font-size:12px;font-weight:700;letter-spacing:.2px;border-radius:2px}
.welcome .btn{left:124px;top:460px;width:144px;height:42px}
.welcome-photo{left:680px;top:52px;width:400px;height:506px;background:linear-gradient(135deg,#d6d6d6 0%,#8e8e8e 55%,#4a4a4a 100%)}

/* provide */
.provide{top:1208px;height:500px}
.section-title{left:0;width:1200px;text-align:center;font-family:"Raleway",sans-serif;font-weight:700;font-size:24px;color:var(--navy);letter-spacing:.5px}
.rule{left:578px;width:44px;height:4px;background:var(--maroon)}
.section-sub{left:0;width:1200px;text-align:center;font-size:13px}
.provide .section-title{top:48px}
.provide .rule{top:89px}
.provide .section-sub{top:112px}
.service{top:190px;width:260px;text-align:center}
.service svg{display:block;margin:0 auto;height:76px}
.service h3{margin-top:30px;font-family:"Open Sans",sans-serif;font-weight:700;font-size:13.5px;color:var(--text-dark)}
.service p{margin-top:12px;font-size:11.5px;line-height:24px;padding:0 16px}

/* careers */
.careers{top:1710px;height:395px}
.careers-bg{position:absolute;inset:0;background:linear-gradient(90deg,#26335e 0%,#3a4a78 45%,#2f3d6c 70%,#1c2857 100%)}
.careers .section-title{top:92px;color:var(--white)}
.careers-copy{left:230px;top:160px;width:740px;text-align:center;color:var(--white);font-size:11.5px;line-height:26px}
.careers .btn{left:528px;top:252px;width:145px;height:42px}

/* testimonials */
.testimonials{top:2105px;height:390px}
.testimonials .section-title{top:62px}
.testimonials .rule{top:101px}
.testimonials .section-sub{top:125px}
.quote{top:195px;width:480px;height:130px}
.avatar{position:absolute;left:0;top:0;width:112px;height:112px;border-radius:50%;border:4px solid #eee;background:radial-gradient(circle at 50% 40%,#c9c1b8,#7d756d)}
.quote-body{position:absolute;left:160px;top:14px;width:300px;font-size:11.5px;line-height:24px;font-style:italic;color:#555}
.quote-open,.quote-close{position:absolute;font-size:30px;color:#ccc;font-family:Georgia,serif}
.quote-open{left:137px;top:0}
.quote-close{left:452px;top:64px}
.quote-name{position:absolute;left:160px;top:100px;font-size:11.5px;font-weight:700;color:var(--maroon)}
.quote-role{position:absolute;left:160px;top:120px;font-size:11px;font-style:italic;color:#777}

/* client names */
.clients{top:2495px;height:110px;border-top:1px solid var(--line)}
.client-row{left:140px;top:48px;width:940px;display:flex;justify-content:space-between;align-items:center}
.client{display:flex;align-items:center;gap:8px;font-weight:700;font-size:16px;color:#8c8c8c}
.client i{width:14px;height:14px;background:#9a9a9a;border-radius:50%}

/* footer */
.site-footer{top:2605px;height:351px;background:var(--footer)}
.foot-col{top:50px;font-size:11.5px;color:var(--footer-text);line-height:22px}
.foot-col h4{font-family:"Open Sans",sans-serif;font-weight:700;font-size:12px;color:var(--white);margin-bottom:14px;letter-spacing:.2px}
.news-item{margin-bottom:12px}
.news-item strong{color:#cfcfcf;font-weight:400}
.news-date{font-size:10px;display:flex;align-items:center;gap:7px;color:#bdbdbd}
.news-date i{width:9px;height:9px;background:#8a8a8a}
.pager{position:absolute;right:0;top:0;color:#ccc;font-size:13px;letter-spacing:8px}
.foot-brand{left:955px;top:70px;width:145px;text-align:center;font-family:"Raleway",sans-serif;font-weight:700;font-size:15px;line-height:20px;color:#5a5a5a}
.foot-brand i{display:block;width:50px;height:50px;margin:0 auto 10px;background:#505050}
.foot-bottom{position:absolute;left:0;bottom:0;width:1200px;height:66px;background:var(--footer-bottom);font-size:11px;color:#9a9a9a}
.copyright{left:100px;top:26px}
.follow{right:100px;top:18px;display:flex;align-items:center;gap:10px}
.follow span{margin-right:4px}
.follow i{width:28px;height:28px;border-radius:50%;background:#5f5f5f}
</style>
</head>
<body>

<header class="site-header">
  <div class="brand abs"><span class="brand-mark"></span><span class="brand-name">Northvale Strategy Partners</span></div>
  <div class="contact-bar abs">
    <span><svg width="14" height="14" viewBox="0 0 24 24"><path fill="#1d2b5c" d="M6.6 10.8a15 15 0 0 0 6.6 6.6l2.2-2.2c.3-.3.7-.4 1-.2 1.1.4 2.3.6 3.6.6.6 0 1 .4 1 1V20c0 .6-.4 1-1 1A17 17 0 0 1 3 4c0-.6.4-1 1-1h3.5c.6 0 1 .4 1 1 0 1.3.2 2.5.6 3.6.1.3 0 .7-.2 1z"/></svg>Call Us : <b>(6120) 418 275</b></span>
    <span><svg width="15" height="12" viewBox="0 0 24 18"><rect x="1" y="1" width="22" height="16" fill="none" stroke="#1d2b5c" stroke-width="2"/><path d="M1 1l11 9 11-9" fill="none" stroke="#1d2b5c" stroke-width="2"/></svg>Email Us : <b>info@northvalestrategy.com</b></span>
  </div>
  <nav class="main-nav abs"><span>HOME</span><span>ABOUT US</span><span>SERVICES</span><span>CAREERS</span><span>TESTIMONIALS</span><span>CONTACT US</span></nav>
</header>

<section class="hero">
  <div class="hero-photo" role="img" aria-label="Lighthouse and red-roofed keeper's house on a rocky coastline under a blue sky"></div>
  <h1 class="hero-title abs">WE ARE A BUSINESS CONSULTING AND<br>EXECUTIVE COACHING FIRM</h1>
  <div class="hero-dots abs"><i></i><i></i><i></i><i></i></div>
</section>

<section class="welcome">
  <div class="welcome-kicker abs">WELCOME TO</div>
  <h2 class="welcome-title abs">NORTHVALE STRATEGY PARTNERS</h2>
  <div class="welcome-copy abs">
    <p>Lorem Ipsum is simply dummy text of the printing and typesetting industry. Lorem Ipsum has been the industry's standard dummy text ever since the 1500s, when an unknown printer took a galley of type and scrambled it to make a type specimen book. It has survived not only five centuries, but also the leap into electronic typesetting, remaining essentially unchanged. It was popularised in the 1960s with the release of Letraset sheets.</p>
    <p>It has survived not only five centuries, but also the leap into electronic typesetting, remaining essentially unchanged. It was popularised in the 1960s with the release of Letraset sheets.</p>
  </div>
  <span class="btn abs">READ MORE INFO</span>
  <div class="welcome-photo abs" role="img" aria-label="Black and white photo collage of a businessman on the phone and working at a laptop"></div>
</section>

<section class="provide">
  <h2 class="section-title abs">WE PROVIDE</h2>
  <div class="rule abs"></div>
  <p class="section-sub abs">Consultative services to business C-suites as well as personal coaching to executives.</p>

  <div class="service abs" style="left:134px">
    <svg viewBox="0 0 110 70" width="110"><path d="M5 30l20-18 18 6 12-4 20 4 20 14-14 18-16 12-20-10-22-10z" fill="none" stroke="#777" stroke-width="2.5" stroke-linejoin="round"/><path d="M43 18l-12 14 8 4 14-10 22 18" fill="none" stroke="#777" stroke-width="2.5"/></svg>
    <h3>CONSULTATIVE</h3>
    <p>Lorem Ipsum is simply dummy text of the printing and typesetting industry. Lorem Ipsum has been the industry's standard dummy text ever since...</p>
  </div>
  <div class="service abs" style="left:465px">
    <svg viewBox="0 0 80 76" width="80"><rect x="6" y="40" width="14" height="32" fill="none" stroke="#777" stroke-width="2.5"/><rect x="30" y="30" width="14" height="42" fill="none" stroke="#777" stroke-width="2.5"/><rect x="54" y="38" width="14" height="34" fill="none" stroke="#777" stroke-width="2.5"/><path d="M6 28L30 12l14 10 26-16" fill="none" stroke="#777" stroke-width="2.5"/><path d="M62 4h10v10" fill="none" stroke="#777" stroke-width="2.5"/></svg>
    <h3>BUSINESS C-SUITES</h3>
    <p>Lorem Ipsum is simply dummy text of the printing and typesetting industry. Lorem Ipsum has been the industry's standard dummy text ever since...</p>
  </div>
  <div class="service abs" style="left:806px">
    <svg viewBox="0 0 96 80" width="96"><circle cx="18" cy="10" r="8" fill="#777"/><path d="M8 22h20v26h-4v30h-12V48H8z" fill="#777"/><path d="M28 26l22-10" stroke="#777" stroke-width="3"/><rect x="42" y="4" width="50" height="34" fill="none" stroke="#777" stroke-width="2.5"/></svg>
    <h3>PERSONAL COACHING</h3>
    <p>Lorem Ipsum is simply dummy text of the printing and typesetting industry. Lorem Ipsum has been the industry's standard dummy text ever since...</p>
  </div>
</section>

<section class="careers">
  <div class="careers-bg" role="img" aria-label="Professionals in a business meeting, overlaid with a navy tint"></div>
  <h2 class="section-title abs">CAREERS</h2>
  <p class="careers-copy abs">Lorem Ipsum is simply dummy text of the printing and typesetting industry. Lorem Ipsum has been the industry's standard dummy text ever since the 1500s, when an unknown printer took a galley of type and scrambled it to make a type specimen book. It has survived not only five centuries, but also the leap into electronic typesetting, remaining essentially unchanged.</p>
  <span class="btn abs">READ MORE INFO</span>
</section>

<section class="testimonials">
  <h2 class="section-title abs">WHAT OUR CLIENT'S SAY</h2>
  <div class="rule abs"></div>
  <p class="section-sub abs">Consultative services to business C-suites as well as personal coaching to executives.</p>

  <div class="quote abs" style="left:100px">
    <div class="avatar" role="img" aria-label="Portrait photo of a client"></div>
    <span class="quote-open">&ldquo;</span>
    <p class="quote-body">Lorem Ipsum is simply dummy text of the printing and typesetting industry. Lorem Ipsum has been the industry's standard dummy text ever since...</p>
    <span class="quote-close">&rdquo;</span>
    <div class="quote-name">MARCUS ELLERY</div>
    <div class="quote-role">Business man</div>
  </div>
  <div class="quote abs" style="left:622px">
    <div class="avatar" role="img" aria-label="Portrait photo of a client"></div>
    <span class="quote-open">&ldquo;</span>
    <p class="quote-body">Lorem Ipsum is simply dummy text of the printing and typesetting industry. Lorem Ipsum has been the industry's standard dummy text ever since...</p>
    <span class="quote-close">&rdquo;</span>
    <div class="quote-name">MARCUS ELLERY</div>
    <div class="quote-role">Business man</div>
  </div>
</section>

<section class="clients">
  <div class="client-row abs">
    <span class="client">Corvent</span>
    <span class="client"><i></i>Halden</span>
    <span class="client">Ashby Works</span>
    <span class="client"><i></i>Marlow &amp; Co</span>
    <span class="client">Petrel</span>
    <span class="client"><i></i>Quillon</span>
  </div>
</section>

<footer class="site-footer">
  <div class="foot-col abs" style="left:100px;width:280px">
    <h4>LATEST NEWS</h4><span class="pager">&lsaquo;&rsaquo;</span>
    <div class="news-item">Simply dummy text of the printing and typesetting <strong>been the industry's standard</strong>
      <div class="news-date"><i></i>Posted on 27 March 2015</div></div>
    <div class="news-item">Simply dummy text of the printing and typesetting <strong>been the industry's standard</strong>
      <div class="news-date"><i></i>Posted on 27 March 2015</div></div>
  </div>
  <div class="foot-col abs" style="left:458px;width:250px">
    <h4>PRIVACY POLICY</h4>
    <p>Lorem Ipsum is simply dummy text of the printing and typesetting industry. Lorem Ipsum has been the industry's standard dummy text ever since the 1500s, when an unknown printer took industry's standard dummy text ever since the 1500s...</p>
  </div>
  <div class="foot-col abs" style="left:783px;width:140px">
    <h4>WELCOME</h4>
    <p>Home<br>About Us<br>Services<br>Careers<br>Testimonials<br>Contact Us</p>
  </div>
  <div class="foot-brand abs"><i></i>Northvale Strategy Partners</div>

  <div class="foot-bottom">
    <span class="copyright abs">© Copyright, 2015. Northvale Strategy Partners. All rights reserved.</span>
    <div class="follow abs"><span>Follow Us :</span><i></i><i></i><i></i><i></i><i></i></div>
  </div>
</footer>

</body>
</html>
```